Australian Trucking Company Requires Professional Looking Stationary

We require a professional looking stationary design that incorporates our newly designed logo.

Our business, called "Brell Haulage Contracting", provides contracting work, transport and logistics to business in Western Australia particularly with links to the mining sector.

We are a small business looking to expand and our new logo and our new stationary will help develop our brand image in our market place.

Target Market(s)

Businesses and Corporation with links to the Mining Sector

Industry/Entity Type

Small Business

Requirements
Must have
• The letterhead must have the following details:
The new logo

Text saying: "Brell Holdings Pty Ltd (ACN 582 316 907) ATF The Brell Discretionary Trust T/AS"
"ABN 71 834 209 553"
Address "P.O Box 817 Wattlegrove WA, 6958"
Phone: 08 9352 7140
Email: brellhaul@mailbox-example.com.au

The text on the letterhead should be editable as the details are likely to change in the near future. Provision should be made for a website address all though one isn't available at the moment.

The styling, layout and font text is entirely up to the designer.

```html
<!DOCTYPE html>
<html lang="en">
<head>
<meta charset="utf-8">
<title>Brell Haulage Contracting — Stationery</title>
<link href="https://fonts.googleapis.com/css2?family=Questrial&display=swap" rel="stylesheet">
<style>
  :root {
    --red: #e3222b;
    --red-deep: #a5141b;
    --red-dark: #7e0d12;
    --paper: #ffffff;
    --ink: #4a4a4a;
    --ink-soft: #777777;
    --stage: #d6d6d6;
    --truck-grey: #e6e6e6;
  }
  * { box-sizing: border-box; margin: 0; padding: 0; }
  html, body { width: 1200px; height: 872px; overflow: hidden; }
  body {
    background: var(--stage);
    font-family: "Questrial", "Century Gothic", sans-serif;
    color: var(--ink);
    position: relative;
  }
  .sheet {
    position: absolute;
    top: 56px;
    width: 537px;
    height: 760px;
    overflow: hidden;
    box-shadow: 0 6px 18px rgba(0,0,0,.25);
  }

  /* ---------- Letterhead ---------- */
  .letterhead { left: 50px; background: var(--paper); }
  .letterhead .truck-mark {
    position: absolute; left: 30px; top: 62px; width: 72px; height: 48px;
    background: linear-gradient(135deg, #9a9a9a, #4d4d4d);
    border-radius: 4px;
  }
  .letterhead .header-band {
    position: absolute; left: 110px; top: 50px; right: 0; height: 70px;
    background: linear-gradient(90deg, var(--red), var(--red-deep));
    clip-path: polygon(18px 0, 100% 0, 100% 100%, 0 100%);
  }
  .letterhead .header-rule {
    position: absolute; left: 300px; right: 0; top: 120px; height: 6px;
    background: var(--red-dark);
  }
  .brand-name {
    position: absolute; color: #fff; text-transform: uppercase;
    font-size: 18px; line-height: 19px; letter-spacing: 1px;
  }
  .letterhead .brand-name { left: 138px; top: 57px; }

  .recipient {
    position: absolute; left: 60px; top: 190px;
    font-size: 9px; line-height: 11px; color: var(--ink-soft);
  }
  .letter-body {
    position: absolute; left: 60px; top: 268px; width: 400px;
    font-size: 9px; line-height: 13px; color: var(--ink-soft);
  }
  .letter-body p { margin-bottom: 12px; }
  .letter-body .salutation { margin-bottom: 14px; }
  .sign-off {
    position: absolute; left: 60px; top: 560px;
    font-size: 9px; line-height: 11px; color: var(--ink-soft);
  }
  .signature {
    width: 60px; height: 16px; margin: 6px 0 6px 10px;
    background: linear-gradient(90deg, #bdbdbd, #8a8a8a);
    border-radius: 8px;
  }
  .watermark-truck {
    position: absolute; right: 30px; bottom: 110px; width: 210px; height: 190px;
    background: linear-gradient(160deg, var(--truck-grey), #f6f6f6);
    border-radius: 10px;
  }
  .letter-footer {
    position: absolute; right: 28px; bottom: 46px; text-align: right;
    font-size: 9px; line-height: 14px; color: var(--ink);
  }
  .letter-footer .contact-line span { white-space: nowrap; }
  .letter-footer svg { width: 9px; height: 9px; vertical-align: -1px; margin: 0 3px 0 10px; }
  .footer-band {
    position: absolute; left: 0; right: 0; bottom: 0; height: 30px;
  }
  .footer-band .abn {
    position: absolute; left: 28px; top: 4px; font-size: 9px; color: var(--red);
  }
  .footer-band .bar {
    position: absolute; left: 0; right: 0; bottom: 0; height: 10px;
    background: linear-gradient(90deg, var(--red), var(--red-deep));
  }

  /* ---------- Red cover sheet ---------- */
  .cover {
    left: 613px;
    background: radial-gradient(ellipse at 20% 10%, var(--red) 0%, #c81a21 45%, var(--red-deep) 100%);
  }
  .cover .truck-mark {
    position: absolute; left: 40px; top: 78px; width: 72px; height: 52px;
    background: linear-gradient(135deg, #ffffff, #e9d2d3);
    border-radius: 4px;
  }
  .cover .brand-name { left: 128px; top: 72px; font-size: 22px; line-height: 23px; }
  .cover .watermark-truck {
    right: 0; bottom: 0; width: 340px; height: 360px;
    background: linear-gradient(150deg, rgba(255,255,255,.10), rgba(90,0,5,.25));
    border-radius: 14px 0 0 0;
  }
</style>
</head>
<body>

<section class="sheet letterhead" aria-label="Letterhead">
  <div class="truck-mark" role="img" aria-label="Truck illustration in grey"></div>
  <div class="header-band"></div>
  <div class="header-rule"></div>
  <div class="brand-name">Brell<br>Haulage<br>Contracting</div>

  <address class="recipient" style="font-style:normal">
    Name<br>Title<br>Company Name<br>Address<br>City, State, Zip Code
  </address>

  <div class="letter-body">
    <p class="salutation">Dear Alex Marlow,</p>
    <p>We write to confirm our haulage schedule for the coming quarter and to outline the routes, loads and timing agreed during our recent meeting at your site office.</p>
    <p>Our fleet will run twice weekly between the depot and the northern pits, with a spare prime mover held on standby for urgent work. Every driver holds current site inductions, and each vehicle is serviced on a fixed cycle. We will send a weekly report showing tonnes moved, kilometres travelled and any delays, so your team can plan ahead with confidence.</p>
    <p>Please contact our office if you need to change pickup times or add loads. We value your business and look forward to working together.</p>
  </div>

  <div class="sign-off">
    Sincerely,
    <div class="signature" role="img" aria-label="Handwritten signature"></div>
    Your Name goes here<br>Consultant Manager
  </div>

  <div class="watermark-truck" role="img" aria-label="Faint truck illustration"></div>

  <footer class="letter-footer">
    <div>Brell Holdings Pty Ltd (ACN 582 316 907) ATF The Brell Discretionary Trust T/AS</div>
    <div class="contact-line">
      <span><svg viewBox="0 0 10 10"><path d="M5 1 L9.5 5 H8 V9 H6 V6.5 H4 V9 H2 V5 H0.5 Z" fill="#e3222b"/></svg>P.O Box 817 Wattlegrove WA, 6958</span>
      <span><svg viewBox="0 0 10 10"><path d="M2 1 C1 1 0.5 2 1 3.5 C2 6 4 8 6.5 9 C8 9.5 9 9 9 8 L7.5 6.5 L6 7.3 C4.5 6.5 3.5 5.5 2.7 4 L3.5 2.5 Z" fill="#e3222b"/></svg>08 9352 7140</span>
      <span><svg viewBox="0 0 10 10"><rect x="0.5" y="2" width="9" height="6.5" fill="#e3222b"/><path d="M0.5 2 L5 5.5 L9.5 2" stroke="#fff" stroke-width="0.8" fill="none"/></svg>brellhaul@mailbox-example.com.au</span>
    </div>
  </footer>

  <div class="footer-band">
    <span class="abn">ABN 71 834 209 553</span>
    <div class="bar"></div>
  </div>
</section>

<section class="sheet cover" aria-label="Red cover sheet">
  <div class="truck-mark" role="img" aria-label="Truck illustration in white"></div>
  <div class="brand-name">Brell<br>Haulage<br>Contracting</div>
  <div class="watermark-truck" role="img" aria-label="Large tone-on-tone truck illustration"></div>
</section>

</body>
</html>
```